Rise Past The Ridge - This will be the titles of the podcast. The podcast is all about self developen

I need a graphic design for a podcast please. This podcast is all about heeling people make a change in their life Topics of business, health and fitness, learning, relationships. Pretty much anything to do with living a legendary life. I have not yet got a logo designed yet but will look at doing this in conjunction with this project.

Target Market(s)

20 - 35 year old males wanting to make a change in their lives and live a legendary life.

Industry/Entity Type

Life Coaching

Font styles to use
Sans Serif
Script

Colors
ffffff
000000
33a6d7

Requirements
Must have
• Simple bold great colours. Simplicity is key
Nice to have
• I have yet to form a logo so I may need one of those built too.
Should not have
• Open to suggestions just not too busy!

```html
<!DOCTYPE html>
<html lang="en">
<head>
<meta charset="utf-8">
<title>Rise Past The Ridge Podcast</title>
<link rel="stylesheet" href="https://fonts.googleapis.com/css2?family=Share+Tech+Mono&display=swap">
<style>
  :root {
    --blue-deep: #0a6896;
    --blue-mid: #0c74a6;
    --blue-brand: #33a6d7;
    --black: #000000;
    --charcoal: #1d1d1d;
    --white: #ffffff;
  }
  html, body {
    margin: 0;
    padding: 0;
    overflow: hidden;
    background: var(--blue-deep);
  }
  .cover {
    position: relative;
    width: 1200px;
    height: 1200px;
    overflow: hidden;
  }
  .cover svg {
    display: block;
  }
  .title-line {
    font-family: "Share Tech Mono", monospace;
    font-size: 138px;
    fill: var(--white);
  }
  .subtitle {
    font-family: "Share Tech Mono", monospace;
    font-size: 46px;
    fill: var(--white);
  }
</style>
</head>
<body>
<div class="cover">
  <svg width="1200" height="1200" viewBox="0 0 1200 1200" xmlns="http://www.w3.org/2000/svg">
    <defs>
      <radialGradient id="bg-glow" cx="50%" cy="50%" r="70%">
        <stop offset="0%" stop-color="var(--blue-brand)"/>
        <stop offset="55%" stop-color="var(--blue-mid)"/>
        <stop offset="100%" stop-color="var(--blue-deep)"/>
      </radialGradient>
      <linearGradient id="facet-left" x1="0" y1="0" x2="1" y2="1">
        <stop offset="0%" stop-color="var(--black)"/>
        <stop offset="100%" stop-color="var(--charcoal)"/>
      </linearGradient>
      <linearGradient id="facet-right" x1="0" y1="0" x2="1" y2="1">
        <stop offset="0%" stop-color="#181818"/>
        <stop offset="100%" stop-color="var(--black)"/>
      </linearGradient>
    </defs>

    <rect class="background-pattern" x="0" y="0" width="1200" height="1200" fill="url(#bg-glow)"
          role="img" aria-label="Blue background with a halftone pattern of small cyan diamonds"/>

    <g class="emblem">
      <polygon class="emblem-backing" points="628,72 1134,628 572,1136 66,574" fill="var(--white)"/>
      <polygon class="emblem-border" points="600,64 1140,602 600,1144 58,602" fill="var(--white)"/>
      <polygon class="facet facet-left" points="600,70 600,1138 64,602" fill="url(#facet-left)"/>
      <polygon class="facet facet-right" points="600,70 1134,602 600,1138" fill="url(#facet-right)"/>
    </g>

    <g class="title">
      <text class="title-line" x="244" y="592" textLength="732" lengthAdjust="spacing">RISE PAST</text>
      <text class="title-line" x="244" y="730" textLength="732" lengthAdjust="spacing">THE RIDGE</text>
    </g>

    <g class="subtitle-group">
      <line x1="420" y1="819" x2="478" y2="819" stroke="var(--white)" stroke-width="3"/>
      <text class="subtitle" x="488" y="822" textLength="222" lengthAdjust="spacing">PODCAST</text>
      <line x1="718" y1="819" x2="776" y2="819" stroke="var(--white)" stroke-width="3"/>
    </g>
  </svg>
</div>
</body>
</html>
```